Business Card Design Project

We need a business card for a new technology services company. We develop software and implement software packages for our business customers and although we will begin with just one or two service offerings, our service offerings will expand over time. Our name comes from the an author, KL Barrow, and his "idea" was that opportunity should be based on ability and achievement, not on social status.

We would like to see a design that is standard in its size and shape, but stands apart in its dramatic color contrasts. The card should not use too many colors - the colors used in the background should highlight the brilliant blues of the logo (see attachment) to dramatic effect. The background should not be white.

If necessary, you can change the color of the words "KL Barrow", but not the word "Idea".

Card size should be U.S. standard 2 inches by 3.5 inches and provide for 1/8 inch bleed area on each side.

We need a design for both sides of the business card, one side communicating the company logo and contact information, the other side being purely graphical, incorporating the logo but no other information.

Contact Information Required:
Kate Brook
KateBrook@klbarrowvista.com
614-387-2259

Target Market(s)

Business executives

Industry/Entity Type

Software

Requirements
Must have
• It must have the full company logo on one side, and at least the graphic element of the logo on the other. Either that or the full logo on both.
Nice to have
• It would be nice to have a design that could work without needing two different textures. For example, it would be nice if the entire card could be shiny, not just parts of the card.

It would also be nice if texture is something we could add later.
Should not have
• The card should not use the color green.

```html
<!DOCTYPE html>
<html lang="en">
<head>
<meta charset="utf-8">
<title>KL Barrow Vista — Business Card</title>
<link rel="stylesheet" href="https://fonts.googleapis.com/css2?family=Open+Sans:wght@300;400;600;700&display=swap">
<style>
  :root {
    --page: #ffffff;
    --card: #1e1e1e;
    --card-glow: #2a2a2a;
    --wordmark: #a9a9a9;
    --blue: #0a93d6;
    --blue-deep: #0676b6;
    --blue-bright: #12acec;
    --text: #ffffff;
    --rule: #8a8a8a;
  }
  * { margin: 0; padding: 0; box-sizing: border-box; }
  html, body {
    width: 1200px; height: 1000px; overflow: hidden;
    background: var(--page);
    font-family: "Open Sans", Arial, sans-serif;
  }
  .card {
    position: absolute; left: 275px; width: 644px; height: 367px;
    background: var(--card); overflow: hidden;
    box-shadow: 4px 5px 8px rgba(0,0,0,0.45);
  }
  .card--front { top: 104px; }
  .card--back  { top: 534px; }

  .symbol-area {
    position: absolute;
    background: radial-gradient(circle at center, rgba(10,147,214,0.35) 0%, rgba(10,147,214,0.12) 40%, rgba(30,30,30,0) 70%);
  }
  .card--front .symbol-area { left: 300px; top: -40px; width: 400px; height: 340px; }
  .texture-area {
    position: absolute;
    background: radial-gradient(ellipse at center, var(--card-glow) 0%, rgba(30,30,30,0) 70%);
  }
  .card--front .texture-area { left: 40px; top: 120px; width: 280px; height: 200px; }
  .card--back .texture-area { left: -40px; top: 60px; width: 260px; height: 300px; }

  .wordmark {
    position: absolute; white-space: nowrap;
    color: var(--wordmark); font-weight: 400; letter-spacing: -1px;
  }
  .card--front .wordmark { left: 44px; top: 272px; font-size: 42px; }
  .website {
    position: absolute; left: 139px; top: 323px;
    color: var(--text); font-size: 15px; letter-spacing: 1.6px;
  }

  .card--back .wordmark { left: 218px; top: 126px; font-size: 38px; }
  .mark-dot {
    position: absolute; left: 528px; top: 76px; width: 34px; height: 34px;
    border-radius: 50%; background: var(--blue);
  }
  .person {
    position: absolute; left: 47px; top: 268px;
    color: var(--blue); font-size: 22px; font-weight: 600;
  }
  .name-rule {
    position: absolute; left: 175px; right: 0; top: 289px;
    height: 2px; background: var(--rule);
  }
  .contacts {
    position: absolute; left: 47px; top: 306px;
    display: flex; gap: 16px; color: var(--text); font-size: 15px;
  }
  .contact { display: flex; align-items: center; gap: 5px; }
  .contact svg { width: 15px; height: 15px; fill: var(--blue); }
  .band {
    position: absolute; left: 25px; width: 596px; top: 350px; height: 60px;
    border-radius: 24px;
    background: linear-gradient(90deg, var(--blue-bright), var(--blue) 50%, var(--blue-deep));
  }
</style>
</head>
<body>
  <section class="card card--front" aria-label="Card front">
    <div class="texture-area" role="img" aria-label="Faint background circle texture"></div>
    <div class="symbol-area" role="img" aria-label="Large blue brand graphic"></div>
    <div class="wordmark">KL Barrow Vista</div>
    <div class="website">www.klbarrowvista.com</div>
  </section>

  <section class="card card--back" aria-label="Card back">
    <div class="texture-area" role="img" aria-label="Faint background circle texture"></div>
    <div class="wordmark">KL Barrow Vista</div>
    <div class="mark-dot"></div>
    <div class="person">Kate Brook</div>
    <div class="name-rule"></div>
    <div class="contacts">
      <span class="contact">
        <svg viewBox="0 0 24 24" aria-hidden="true"><path d="M6.6 10.8a15.1 15.1 0 0 0 6.6 6.6l2.2-2.2c.3-.3.7-.4 1-.2 1.1.4 2.3.6 3.6.6.6 0 1 .4 1 1V20c0 .6-.4 1-1 1A17 17 0 0 1 3 4c0-.6.4-1 1-1h3.5c.6 0 1 .4 1 1 0 1.3.2 2.5.6 3.6.1.3 0 .7-.2 1z"/></svg>
        614-387-2259
      </span>
      <span class="contact">
        <svg viewBox="0 0 24 24" aria-hidden="true"><path d="M2 5h20v14H2z" fill="var(--blue)"/><path d="M3 6l9 7 9-7" fill="none" stroke="#1e1e1e" stroke-width="1.6"/></svg>
        KateBrook@klbarrowvista.com
      </span>
      <span class="contact">
        <svg viewBox="0 0 24 24" aria-hidden="true"><circle cx="12" cy="12" r="10" fill="none" stroke="var(--blue)" stroke-width="2"/><ellipse cx="12" cy="12" rx="4" ry="10" fill="none" stroke="var(--blue)" stroke-width="1.6"/><path d="M2 12h20M4 7h16M4 17h16" stroke="var(--blue)" stroke-width="1.4"/></svg>
        klbarrowvista.com
      </span>
    </div>
    <div class="band"></div>
  </section>
</body>
</html>
```